High-Converting Facebook Ads for Portals Drapes & Louvres (6 Products)

We are looking for a graphic designer to create high-quality Facebook & Instagram ads for our business: Portals Drapes and Louvres (Melbourne, Australia).

We require 6 separate ad designs, each for a different product:

Zipscreen Blinds

Outdoor Awnings

Plantation Shutters

Roller Shutters

Security Doors

Roller Blinds & Sheer Curtains

Ad Specifications:

Sizes:

1440 x 1800 px (4:5 ratio)

1080 x 1080 px (1:1 ratio)

1080 x 1920 px (9:16 ratio for Stories/Reels)

Format: PNG (high resolution, not blurry)

Designed specifically for Meta (Facebook/Instagram ads)

Mobile-friendly layout (clear, easy to read)

Style:

Bold, sales-driven, retail-style ads (NOT minimal)

Eye-catching and designed to generate leads

Clean, professional layout

Similar to promotional home improvement ads

Brand Colours:

Red: #E31E24

Blue: #0072BC

White backgrounds

Each ad must include:

“SALE NOW ON” banner at top

Our showroom address:
482 Upper Wattleby Road, Kestrel Heights (must be fully visible, not cut off)

Phone number: 9471 2658

Our logo (provided)

Badge: “Celebrating 13 YEARS in Business” (must be clean and readable)

Call to Action:

For 5 ads: “Book a FREE quote TODAY!”

For Security Doors ad: “ORDER NOW”

Offers / Pricing:

Most products: “UP TO 40% OFF”

Plantation Shutters: “FROM $299/sqm”

Security Doors: “FROM $750”

Content for each ad (examples):

Zipscreen Blinds:

Made to Measure

Fully Installed

Wind, Sun & Insect Protection

Outdoor Awnings:

Reduce Heat & Glare

Energy Saving

Custom Made

Plantation Shutters:

Modern & Elegant

Light & Privacy Control

Durable & Easy Care

Roller Shutters:

Security Protection

Block Heat & Noise

Total Light Control

Security Doors:

3 Point Locking

Premium Mesh

Custom Made

Blinds & Sheers:

Huge Range of Fabrics

Modern Soft Finish

Perfect for Any Room

Important Notes:

All text must be sharp and easy to read (no blur)

Layout must be balanced and not overcrowded

Ensure no text is cut off (especially address and headings)

Badge text must be straight and professional (no distortion)

Use high-quality, relevant images (we will provide references)

Goal:
Create ads that look professional, trustworthy, and generate enquiries/bookings for in-home quotes.

We are open to creative ideas but want a strong, bold retail-style ad that converts.
I have uploaed chatgpt mocks

Target Market(s)

Homeowners in Melbourne, Australia (typically aged 30–65) looking to improve their homes with blinds, shutters, awnings and security doors. Mid to high income households focused on quality, security, and modern home upgrades.

Industry/Entity Type

Home Improvement / Construction / Retail

Font styles to use
Sans Serif

Requirements
Must have
• Clear, bold and easy-to-read text (must be readable on mobile) High-quality, non-blurry design Strong “SALE” style layout (retail promotional look) Proper spacing (no overcrowded designs) All key info visible (address must NOT be cut off) Correct pricing and offers included Clean “13 YEARS” badge (no distortion or curved text) Consistent branding across all 6 ads
Nice to have
• Modern, slightly premium feel while still being bold Good use of contrast (red/blue/white) Subtle shadows or layering to improve depth Clean use of icons or bullet points Strong hierarchy (headline → benefits → offer → CTA) Variations in layout for testing different ad styles
Should not have
• Minimal or plain designs (we want bold, sales-driven ads) Hard-to-read fonts or script fonts Low-quality or blurry images Overcrowded layouts with too much text Important text cut off (especially address or headings) Overuse of effects or “cheap” looking graphics Yellow-heavy colour schemes (must follow brand colours)

```html
<!DOCTYPE html>
<html lang="en">
<head>
<meta charset="utf-8">
<title>Portals Drapes &amp; Louvres – Sale Ads 4:5</title>
<link rel="stylesheet" href="https://fonts.googleapis.com/css2?family=Oswald:wght@400;500;600;700&family=Tinos:wght@400;700&family=Montserrat:wght@600;800&display=swap">
<style>
  :root{
    --board:#2b2b2b;
    --red:#e31e24;
    --blue:#0072bc;
    --white:#ffffff;
    --ink:#1c1c1c;
    --gold-1:#f7d774;
    --gold-2:#c8932a;
    --gold-3:#7a4f10;
    --num-grad:linear-gradient(180deg,#e31e24 0%,#b2264a 45%,#1a5fb4 100%);
  }
  *{box-sizing:border-box;margin:0;padding:0}
  html,body{width:1200px;height:1114px;overflow:hidden;background:var(--board)}
  .board{position:relative;width:1200px;height:1114px}
  .board-title{position:absolute;top:70px;left:0;width:100%;text-align:center;
    font:500 22px/1 "Oswald",sans-serif;color:var(--white);letter-spacing:.2px}

  .ad{position:absolute;width:312px;height:390px;background:var(--white);overflow:hidden}
  .col-1{left:111px}.col-2{left:444px}.col-3{left:777px}
  .row-1{top:155px}.row-2{top:568px}

  .ad-top{position:absolute;top:0;left:0;width:100%;height:49px;background:var(--red)}
  .ad-top span{position:absolute;left:23px;top:9px;font:400 28px/1 "Tinos",serif;color:var(--white);letter-spacing:.3px}
  .ad-title{position:absolute;top:49px;left:0;width:100%;height:33px;
    background:linear-gradient(90deg,var(--blue) 0%,var(--blue) 45%,rgba(0,114,188,0) 85%)}
  .ad-title span{position:absolute;left:22px;top:1px;font:500 25px/1.2 "Oswald",sans-serif;color:var(--white)}

  .ad-photo{position:absolute;top:82px;right:0;width:66%;height:201px}
  .photo-zip{background:linear-gradient(90deg,rgba(255,255,255,1) 0%,rgba(255,255,255,0) 35%),linear-gradient(180deg,#d9dde0 0%,#6e7274 45%,#8a9a6a 85%,#7b8a5c 100%)}
  .photo-awning{background:linear-gradient(90deg,rgba(255,255,255,1) 0%,rgba(255,255,255,0) 40%),linear-gradient(200deg,#5f8fc4 0%,#b9d0e8 40%,#dfe3e8 70%,#8d949a 100%)}
  .photo-plantation{background:linear-gradient(90deg,rgba(255,255,255,1) 0%,rgba(255,255,255,0) 35%),linear-gradient(180deg,#c9cdd1 0%,#9aa1a8 50%,#d6d6d8 80%,#8b7a68 100%)}
  .photo-roller{background:linear-gradient(90deg,rgba(255,255,255,1) 0%,rgba(255,255,255,0) 40%),linear-gradient(180deg,#eef0f1 0%,#c9cbcc 50%,#8e9092 80%,#4b4d4f 100%)}
  .photo-security{background:linear-gradient(90deg,rgba(255,255,255,1) 0%,rgba(255,255,255,0) 35%),linear-gradient(180deg,#d7e2ea 0%,#6d9ab8 35%,#6f8a4a 65%,#7a5a3a 100%)}
  .photo-sheers{background:linear-gradient(90deg,rgba(255,255,255,1) 0%,rgba(255,255,255,0) 35%),linear-gradient(180deg,#e9ebec 0%,#9b9c9c 40%,#4f4d4c 70%,#e6cfc0 100%)}

  .badge{position:absolute;top:2px;left:226px;width:76px;height:76px}

  .benefits{position:absolute;top:99px;left:22px;list-style:none}
  .benefits li{position:relative;padding-left:16px;font:500 11.5px/17px "Oswald",sans-serif;color:var(--ink)}
  .benefits li::before{content:"";position:absolute;left:0;top:4px;width:8px;height:8px;
    background:repeating-linear-gradient(180deg,var(--red) 0 1.5px,#f6b3b5 1.5px 2.5px)}
  .benefits li.wrap{line-height:14px;margin-top:2px}

  .offer{position:absolute;left:16px}
  .offer-zip{top:171px}.offer-awning{top:160px}.offer-roller{top:170px}.offer-sheers{top:170px}
  .offer-label{font:700 15px/1 "Tinos",serif;color:var(--blue);margin-left:1px}
  .offer-row{display:flex;align-items:flex-start;margin-top:1px}
  .grad{background:var(--num-grad);-webkit-background-clip:text;background-clip:text;color:transparent}
  .offer-num{font:700 94px/.84 "Oswald",sans-serif;letter-spacing:-3px}
  .offer-side{display:flex;flex-direction:column;margin-left:4px;margin-top:4px}
  .offer-pct{font:500 52px/.8 "Oswald",sans-serif}
  .offer-off{font:700 30px/.9 "Oswald",sans-serif;margin-top:2px}
  .burst{position:absolute;width:22px;height:22px}

  .price{position:absolute;left:13px}
  .price-plantation{top:157px}.price-security{top:171px;left:24px}
  .price-label{font:700 15px/1 "Tinos",serif;color:var(--blue);margin-left:2px}
  .price-num{font:700 68px/.9 "Oswald",sans-serif;letter-spacing:-1px}
  .price-unit{font:500 30px/1 "Oswald",sans-serif;text-align:right;margin-top:2px}

  .ad-cta{position:absolute;top:283px;left:0;width:100%;height:45px;background:var(--red);
    display:flex;align-items:center;justify-content:center}
  .ad-cta span{font:600 29px/1 "Oswald",sans-serif;color:var(--white);letter-spacing:-.3px}
  .ad-cta .order{font:400 33px/1 "Tinos",serif;letter-spacing:.5px}

  .ad-foot{position:absolute;top:328px;left:0;width:100%;height:62px;background:var(--blue)}
  .brand{position:absolute;left:11px;top:12px;width:78px;display:flex;flex-direction:column;align-items:center}
  .brand-mark{width:12px;height:12px;background:var(--white);margin-bottom:4px}
  .brand-name{font:600 8.5px/1.15 "Montserrat",sans-serif;color:var(--white);text-align:center}
  .phone{position:absolute;left:104px;top:5px;display:flex;align-items:center}
  .phone svg{width:13px;height:13px;margin-right:7px}
  .phone span{font:800 29px/1 "Montserrat",sans-serif;color:var(--white);letter-spacing:.6px}
  .address{position:absolute;left:105px;top:40px;display:flex;align-items:center}
  .address svg{width:9px;height:12px;margin-right:10px}
  .address span{font:400 10.5px/1 "Oswald",sans-serif;color:var(--white)}
</style>
</head>
<body>
<svg width="0" height="0" style="position:absolute" aria-hidden="true">
  <defs>
    <radialGradient id="goldFill" cx="45%" cy="35%" r="70%">
      <stop offset="0" stop-color="#f7d774"/><stop offset=".6" stop-color="#c8932a"/><stop offset="1" stop-color="#7a4f10"/>
    </radialGradient>
    <symbol id="badge" viewBox="0 0 74 74">
      <circle cx="37" cy="37" r="36" fill="url(#goldFill)"/>
      <circle cx="37" cy="37" r="31" fill="#1b1306" stroke="#f7d774" stroke-width="1.2"/>
      <text x="37" y="19" text-anchor="middle" font-family="Oswald,sans-serif" font-weight="600" font-size="7" letter-spacing=".3" fill="#ffe9a6">CELEBRATING</text>
      <text x="37" y="41" text-anchor="middle" font-family="Tinos,serif" font-weight="700" font-size="23" fill="#f7d774">13</text>
      <rect x="13" y="43" width="48" height="11" rx="1" fill="url(#goldFill)"/>
      <text x="37" y="52" text-anchor="middle" font-family="Oswald,sans-serif" font-weight="700" font-size="9.5" letter-spacing=".5" fill="#1b1306">YEARS</text>
      <text x="37" y="62" text-anchor="middle" font-family="Oswald,sans-serif" font-weight="600" font-size="6.5" letter-spacing=".3" fill="#ffe9a6">IN BUSINESS</text>
    </symbol>
    <symbol id="phone" viewBox="0 0 24 24">
      <path fill="#fff" d="M6.6 10.8c1.4 2.8 3.8 5.1 6.6 6.6l2.2-2.2c.3-.3.7-.4 1-.2 1.1.4 2.3.6 3.6.6.6 0 1 .4 1 1V20c0 .6-.4 1-1 1C10.6 21 3 13.4 3 4c0-.6.4-1 1-1h3.5c.6 0 1 .4 1 1 0 1.3.2 2.5.6 3.6.1.3 0 .7-.2 1z"/>
    </symbol>
    <symbol id="pin" viewBox="0 0 18 24">
      <path fill="#fff" d="M9 0C4 0 0 4 0 9c0 6.8 9 15 9 15s9-8.2 9-15c0-5-4-9-9-9zm0 12.5A3.5 3.5 0 1 1 9 5.5a3.5 3.5 0 0 1 0 7z"/>
    </symbol>
    <symbol id="burst" viewBox="0 0 22 22">
      <path fill="#1c1c1c" d="M9 0l4 1-3 8zM16 4l4 3-8 5zM1 4l3-1 2 7z"/>
    </symbol>
  </defs>
</svg>

<main class="board">
  <h1 class="board-title">1440 x 1800 px (4:5 ratio)</h1>

  <!-- Zipscreen Blinds -->
  <article class="ad col-1 row-1">
    <div class="ad-photo photo-zip" role="img" aria-label="Photo of a patio with grey zipscreen blinds lowered"></div>
    <header class="ad-top"><span>SALE NOW ON</span></header>
    <div class="ad-title"><span>Zipscreen Blinds</span></div>
    <svg class="badge" role="img" aria-label="Celebrating 13 years in business"><use href="#badge"/></svg>
    <ul class="benefits">
      <li>Made to Measure</li><li>Fully Installed</li><li class="wrap">Wind, Sun &amp; Insect<br>Protection</li>
    </ul>
    <div class="offer offer-zip">
      <div class="offer-label">UP TO</div>
      <div class="offer-row"><span class="offer-num grad">40</span><span class="offer-side"><span class="offer-pct grad">%</span><span class="offer-off grad">OFF</span></span></div>
      <svg class="burst" style="left:128px;top:16px"><use href="#burst"/></svg>
    </div>
    <div class="ad-cta"><span>Book a FREE quote TODAY!</span></div>
    <footer class="ad-foot">
      <div class="brand"><span class="brand-mark"></span><span class="brand-name">Portals Drapes<br>&amp; Louvres</span></div>
      <div class="phone"><svg><use href="#phone"/></svg><span>9471 2658</span></div>
      <div class="address"><svg><use href="#pin"/></svg><span>482 Upper Wattleby Road, Kestrel Heights</span></div>
    </footer>
  </article>

  <!-- Outdoor Awnings -->
  <article class="ad col-2 row-1">
    <div class="ad-photo photo-awning" role="img" aria-label="Photo of a striped outdoor awning on a house against the sky"></div>
    <header class="ad-top"><span>SALE NOW ON</span></header>
    <div class="ad-title"><span>Outdoor Awnings</span></div>
    <svg class="badge" role="img" aria-label="Celebrating 13 years in business"><use href="#badge"/></svg>
    <ul class="benefits">
      <li>Reduce Heat &amp; Glare</li><li>Energy Saving</li><li>Custom Made</li>
    </ul>
    <div class="offer offer-awning">
      <div class="offer-label">UP TO</div>
      <div class="offer-row"><span class="offer-num grad">40</span><span class="offer-side"><span class="offer-pct grad">%</span><span class="offer-off grad">OFF</span></span></div>
      <svg class="burst" style="left:128px;top:16px"><use href="#burst"/></svg>
    </div>
    <div class="ad-cta"><span>Book a FREE quote TODAY!</span></div>
    <footer class="ad-foot">
      <div class="brand"><span class="brand-mark"></span><span class="brand-name">Portals Drapes<br>&amp; Louvres</span></div>
      <div class="phone"><svg><use href="#phone"/></svg><span>9471 2658</span></div>
      <div class="address"><svg><use href="#pin"/></svg><span>482 Upper Wattleby Road, Kestrel Heights</span></div>
    </footer>
  </article>

  <!-- Plantation Shutters -->
  <article class="ad col-3 row-1">
    <div class="ad-photo photo-plantation" role="img" aria-label="Photo of a bedroom window fitted with white plantation shutters"></div>
    <header class="ad-top"><span>SALE NOW ON</span></header>
    <div class="ad-title"><span>Plantation Shutters</span></div>
    <svg class="badge" role="img" aria-label="Celebrating 13 years in business"><use href="#badge"/></svg>
    <ul class="benefits">
      <li>Modern &amp; Elegant</li><li>Light &amp; Privacy Control</li><li>Durable &amp; Easy Care</li>
    </ul>
    <div class="price price-plantation">
      <div class="price-label">FROM</div>
      <div class="price-num grad">$299</div>
      <div class="price-unit grad">/sqm</div>
    </div>
    <div class="ad-cta"><span>Book a FREE quote TODAY!</span></div>
    <footer class="ad-foot">
      <div class="brand"><span class="brand-mark"></span><span class="brand-name">Portals Drapes<br>&amp; Louvres</span></div>
      <div class="phone"><svg><use href="#phone"/></svg><span>9471 2658</span></div>
      <div class="address"><svg><use href="#pin"/></svg><span>482 Upper Wattleby Road, Kestrel Heights</span></div>
    </footer>
  </article>

  <!-- Roller Shutters -->
  <article class="ad col-1 row-2">
    <div class="ad-photo photo-roller" role="img" aria-label="Photo of a bright living room with a grey roller blind and floor lamp"></div>
    <header class="ad-top"><span>SALE NOW ON</span></header>
    <div class="ad-title"><span>Roller Shutters</span></div>
    <svg class="badge" role="img" aria-label="Celebrating 13 years in business"><use href="#badge"/></svg>
    <ul class="benefits">
      <li>Security Protection</li><li>Block Heat &amp; Noise</li><li>Total Light Control</li>
    </ul>
    <div class="offer offer-roller">
      <div class="offer-label">UP TO</div>
      <div class="offer-row"><span class="offer-num grad">40</span><span class="offer-side"><span class="offer-pct grad">%</span><span class="offer-off grad">OFF</span></span></div>
      <svg class="burst" style="left:128px;top:16px"><use href="#burst"/></svg>
    </div>
    <div class="ad-cta"><span>Book a FREE quote TODAY!</span></div>
    <footer class="ad-foot">
      <div class="brand"><span class="brand-mark"></span><span class="brand-name">Portals Drapes<br>&amp; Louvres</span></div>
      <div class="phone"><svg><use href="#phone"/></svg><span>9471 2658</span></div>
      <div class="address"><svg><use href="#pin"/></svg><span>482 Upper Wattleby Road, Kestrel Heights</span></div>
    </footer>
  </article>

  <!-- Security Doors -->
  <article class="ad col-2 row-2">
    <div class="ad-photo photo-security" role="img" aria-label="Photo of a security mesh door opening onto a balcony with a bay view"></div>
    <header class="ad-top"><span>SALE NOW ON</span></header>
    <div class="ad-title"><span>Security Doors</span></div>
    <svg class="badge" role="img" aria-label="Celebrating 13 years in business"><use href="#badge"/></svg>
    <ul class="benefits">
      <li>3 Point Locking</li><li>Premium Mesh</li><li>Custom Made</li>
    </ul>
    <div class="price price-security">
      <div class="price-label">FROM</div>
      <div class="price-num grad">$750</div>
    </div>
    <div class="ad-cta"><span class="order">ORDER NOW</span></div>
    <footer class="ad-foot">
      <div class="brand"><span class="brand-mark"></span><span class="brand-name">Portals Drapes<br>&amp; Louvres</span></div>
      <div class="phone"><svg><use href="#phone"/></svg><span>9471 2658</span></div>
      <div class="address"><svg><use href="#pin"/></svg><span>482 Upper Wattleby Road, Kestrel Heights</span></div>
    </footer>
  </article>

  <!-- Blinds & Sheers -->
  <article class="ad col-3 row-2">
    <div class="ad-photo photo-sheers" role="img" aria-label="Photo of a bedroom with full-length grey sheer curtains"></div>
    <header class="ad-top"><span>SALE NOW ON</span></header>
    <div class="ad-title"><span>Blinds &amp; Sheers</span></div>
    <svg class="badge" role="img" aria-label="Celebrating 13 years in business"><use href="#badge"/></svg>
    <ul class="benefits">
      <li>Huge Range of Fabrics</li><li>Modern Soft Finish</li><li>Perfect for Any Room</li>
    </ul>
    <div class="offer offer-sheers">
      <div class="offer-label">UP TO</div>
      <div class="offer-row"><span class="offer-num grad">40</span><span class="offer-side"><span class="offer-pct grad">%</span><span class="offer-off grad">OFF</span></span></div>
      <svg class="burst" style="left:128px;top:16px"><use href="#burst"/></svg>
    </div>
    <div class="ad-cta"><span>Book a FREE quote TODAY!</span></div>
    <footer class="ad-foot">
      <div class="brand"><span class="brand-mark"></span><span class="brand-name">Portals Drapes<br>&amp; Louvres</span></div>
      <div class="phone"><svg><use href="#phone"/></svg><span>9471 2658</span></div>
      <div class="address"><svg><use href="#pin"/></svg><span>482 Upper Wattleby Road, Kestrel Heights</span></div>
    </footer>
  </article>
</main>
</body>
</html>
```